Graphic Design for a 3 Banner Tradeshow Setup

We are a Pipe Restoration company that specializes in trenchless pipelining. We need a design for a 3 banner setup to use at tradeshows. See attached "banner specs" for sizing - note the 48" x 92" will be in between the two 36" x 92" banners. See attached "Mock-Up" of information each banner needs and utilize the color scheme of the banners we already have in the "both DWM banners" AI file attached. The final designs should communicate what we do and attract people into our booth. We would like to have graphics of realistic pipes for a before (dirty pipe), after cleaning pipe, and lined pipe - see example of "pipe pictures" attached. I'm not sure if this is something you can generate or if we will need to find images of our own to send. Also, see attached "screenshot-process" to see similar images we would like to use to showcase the process.
Target Market(s)
Homeowners, Property Managers, HOA Communities, Healthcare Facilities & Hospitals, and commercial properties
Industry/Entity Type
Trenchless Pipelining
Look and feel

```html
<!DOCTYPE html>
<html lang="en">
<head>
<meta charset="utf-8">
<title>DWM Tradeshow Banners</title>
<link href="https://fonts.googleapis.com/css2?family=Krona+One&family=Barlow:wght@500;600&family=Barlow+Condensed:wght@600;700&display=swap" rel="stylesheet">
<style>
:root{
  --navy:#0d1a33;
  --navy-deep:#081226;
  --royal:#1d3f8f;
  --blue:#1a6fc0;
  --cyan:#1ea6e0;
  --sky:#dcedf9;
  --ink:#0c1424;
  --white:#ffffff;
  --ring:#cfd3d8;
}
*{box-sizing:border-box;margin:0;padding:0}
html,body{width:1200px;height:920px;overflow:hidden;background:#fff}
.stand{position:relative;width:1200px;height:920px;font-family:"Krona One",sans-serif;color:var(--ink)}
.banner{position:absolute;top:0;height:920px;overflow:hidden}
.banner--side{width:360px;background:linear-gradient(180deg,var(--navy-deep) 0%,var(--navy) 30%,#123a78 55%,var(--cyan) 70%,var(--navy-deep) 80%)}
.banner--left{left:0}
.banner--right{left:840px}
.banner--center{left:360px;width:480px;background:var(--white)}

.brand{position:absolute;left:40px;top:40px;width:286px}
.brand__row{display:flex;align-items:center;gap:10px}
.brand__mark{width:50px;height:50px;background:linear-gradient(135deg,var(--cyan),var(--royal));border-radius:4px}
.brand__name{font-size:50px;line-height:50px;color:var(--white);letter-spacing:2px}
.brand__tag{margin-top:10px;font-family:"Barlow",sans-serif;font-weight:600;font-size:11.5px;letter-spacing:3.2px;color:var(--white);white-space:nowrap}

.card{position:absolute;top:140px;height:600px;border-radius:18px;border:2px solid var(--cyan);
  background:linear-gradient(180deg,#eef6fc 0%,#cfe4f5 45%,#f2f8fd 100%)}
.banner--left .card{left:37px;width:288px}
.banner--right .card{left:32px;width:295px}
.card__tab{position:absolute;left:50%;top:-10px;transform:translateX(-50%);width:200px;height:36px;
  background:linear-gradient(180deg,var(--cyan),var(--royal));clip-path:polygon(0 0,100% 0,88% 100%,12% 100%);
  color:var(--white);font-size:17px;line-height:36px;text-align:center}
.icon{width:74px;height:72px;border-radius:6px;background:linear-gradient(180deg,var(--cyan),var(--royal));
  border:2px solid #8fd0f2;display:flex;align-items:center;justify-content:center}
.icon svg{width:48px;height:48px;fill:none;stroke:#fff;stroke-width:2.2;stroke-linecap:round;stroke-linejoin:round}

.assess{position:absolute;left:0;width:100%;text-align:center}
.assess .icon{margin:0 auto}
.assess__label{margin-top:6px;font-size:17px;line-height:21px;color:var(--ink)}

.fix{position:absolute;left:27px;display:flex;align-items:center;gap:13px}
.fix__label{font-size:18px;line-height:22px;color:var(--ink)}

.photo{position:absolute;left:0;top:745px;width:360px;height:175px}
.photo--control{background:linear-gradient(160deg,#2a3f72 0%,#5a6f9c 40%,#1b2540 100%)}
.photo--crew{background:linear-gradient(160deg,#4a5a3c 0%,#2c3a2a 45%,#1f7a46 80%,#101510 100%)}

.headline{position:absolute;left:0;width:480px;text-align:center;
  background:linear-gradient(180deg,var(--royal),var(--cyan));-webkit-background-clip:text;background-clip:text;color:transparent}
.headline--big{top:22px;font-size:78px;line-height:84px;transform:scaleY(1.2);letter-spacing:2px}
.headline--sub{top:110px;font-size:41px;line-height:46px;background:linear-gradient(180deg,var(--royal),var(--blue));-webkit-background-clip:text;background-clip:text}

.band{position:absolute;left:0;top:167px;width:480px;height:134px;background:linear-gradient(180deg,var(--royal) 0%,var(--cyan) 100%);
  text-align:center;color:var(--white)}
.band__small{padding-top:25px;font-size:17px;letter-spacing:1px}
.band__large{margin-top:8px;font-size:27.5px;line-height:36px;text-shadow:2px 2px 0 var(--navy)}

.process{position:absolute;left:0;top:301px;width:480px;height:480px}
.process svg.ring{position:absolute;left:0;top:0}
.art{position:absolute;border-radius:8px}
.art--clean{left:62px;top:28px;width:151px;height:137px;background:linear-gradient(135deg,#6b6e73,#8a6a3e 45%,#c9cdd2);clip-path:polygon(12% 0,100% 72%,88% 100%,0 28%)}
.art--liner{left:276px;top:28px;width:153px;height:137px;background:linear-gradient(135deg,#7d8288,var(--cyan) 55%,#0f6bb0);clip-path:polygon(88% 0,100% 28%,12% 100%,0 72%)}
.art--blocked{left:18px;top:200px;width:181px;height:96px;background:linear-gradient(180deg,#6a6d72,#7b5a34 50%,#3d3f44);clip-path:polygon(4% 0,100% 40%,96% 100%,0 62%)}
.art--lined{left:281px;top:239px;width:167px;height:66px;background:linear-gradient(180deg,#9aa0a6,var(--cyan) 35%,#1763b6)}
.art--before{left:95px;top:351px;width:134px;height:115px;border-radius:50% 40% 40% 50%;background:radial-gradient(circle at 40% 50%,#0a0a0a 40%,#6b4a30 55%,#4f6378 80%)}
.art--after{left:243px;top:326px;width:175px;height:140px;border-radius:40% 50% 50% 40%;background:radial-gradient(circle at 62% 45%,#0d5ea6 40%,#6fd3ef 52%,#4a3a32 75%)}
.art__tag{position:absolute;font-family:"Barlow Condensed",sans-serif;font-weight:700;font-size:15px;color:#fff}
.badge{position:absolute;width:36px;height:36px;border-radius:50%;background:var(--blue);border:3px solid #fff;box-shadow:0 0 0 1.5px var(--blue);
  color:#fff;font-size:18px;line-height:30px;text-align:center}
.caption{position:absolute;font-family:"Barlow",sans-serif;font-weight:500;font-size:12px;line-height:13px;color:var(--ink)}

.cta{position:absolute;left:21px;top:795px;width:438px;height:125px;border-radius:18px 18px 0 0;background:linear-gradient(180deg,#050709,#1a1c20);text-align:center}
.cta__pill{position:absolute;left:48px;top:783px;width:381px;height:33px;border-radius:5px;background:var(--cyan);
  font-family:"Barlow Condensed",sans-serif;font-weight:600;font-size:18.5px;line-height:33px;color:#fff;text-align:center;letter-spacing:.3px}
.cta__web{position:absolute;left:0;width:100%;top:36px;font-size:19px;color:var(--cyan)}
.cta__phone{position:absolute;left:0;width:100%;top:66px;font-size:27px;color:#fff}
</style>
</head>
<body>
<main class="stand">

  <section class="banner banner--side banner--left">
    <div class="brand">
      <div class="brand__row"><span class="brand__mark"></span><span class="brand__name">DWM</span></div>
      <div class="brand__tag">DURABLE WATERLINE METHODS</div>
    </div>
    <div class="card">
      <div class="card__tab">WE ASSESS</div>
      <div class="assess" style="top:44px">
        <div class="icon"><svg viewBox="0 0 48 48"><rect x="8" y="12" width="12" height="10" rx="2"/><path d="M14 22v14M28 10v26a4 4 0 0 0 8 0V10"/><path d="M14 12V6h10"/></svg></div>
        <div class="assess__label">CCTV PIPE<br>INVESTIGATION</div>
      </div>
      <div class="assess" style="top:177px">
        <div class="icon"><svg viewBox="0 0 48 48"><path d="M4 16l8-2 10 6 6-3 8 1 8 2v12l-8 2-10 8-6-4-6-2-10-6z"/><path d="M18 26l6 6M22 24l6 6"/></svg></div>
        <div class="assess__label">SCOPE<br>DEVELOPMENT</div>
      </div>
      <div class="assess" style="top:313px">
        <div class="icon"><svg viewBox="0 0 48 48"><rect x="10" y="4" width="22" height="38" rx="3"/><rect x="14" y="9" width="14" height="7"/><path d="M15 22h2M20 22h2M15 28h2M20 28h2M15 34h2M20 34h2"/><circle cx="35" cy="30" r="7"/><path d="M35 26v8"/></svg></div>
        <div class="assess__label">BUDGETARY<br>EVALUATION</div>
      </div>
      <div class="assess" style="top:452px">
        <div class="icon"><svg viewBox="0 0 48 48"><circle cx="24" cy="22" r="12"/><path d="M24 10v24M12 22h24M15 31l-9 9"/><path d="M36 6v34"/></svg></div>
        <div class="assess__label">PROJECT<br>OVERSIGHT</div>
      </div>
    </div>
    <div class="photo photo--control" role="img" aria-label="Photo of a technician reviewing sewer camera footage at a workstation"></div>
  </section>

  <section class="banner banner--center">
    <h1 class="headline headline--big">PIPE</h1>
    <h2 class="headline headline--sub">PROBLEMS?</h2>
    <div class="band">
      <p class="band__small">WE HELP FIX PIPE PROBLEMS</p>
      <p class="band__large">WITHOUT HAVING TO<br>TEAR UP YOUR BUIDLING</p>
    </div>

    <div class="process">
      <svg class="ring" width="480" height="480" viewBox="0 0 480 480"><circle cx="243" cy="247" r="148" fill="none" stroke="var(--ring)" stroke-width="6"/></svg>
      <div class="art art--clean" role="img" aria-label="Illustration of a cutting tool cleaning a blocked pipe"></div>
      <div class="art art--liner" role="img" aria-label="Illustration of a liner and inflated bladder inside a pipe"></div>
      <div class="art art--blocked" role="img" aria-label="Illustration of a cut-away pipe blocked by scale and roots"></div>
      <div class="art art--lined" role="img" aria-label="Illustration of a finished lined pipe"></div>
      <div class="art art--before" role="img" aria-label="Illustration of a corroded pipe end before lining"><span class="art__tag" style="left:28px;top:48px">BEFORE</span></div>
      <div class="art art--after" role="img" aria-label="Illustration of a pipe end with blue liner after lining"><span class="art__tag" style="left:74px;top:46px">AFTER</span></div>

      <div class="badge" style="left:86px;top:302px">1</div>
      <div class="badge" style="left:103px;top:155px">2</div>
      <div class="badge" style="left:225px;top:90px">3</div>
      <div class="badge" style="left:345px;top:168px">4</div>

      <p class="caption" style="left:27px;top:296px;width:70px">A sewer<br>camera<br>reveals a<br>blocked<br>brenched<br>and or root<br>interupted<br>pipe</p>
      <p class="caption" style="left:27px;top:130px;width:90px">The pipe is<br>cleaned with<br>a scropion<br>cutting tool</p>
      <p class="caption" style="left:229px;top:29px;width:100px">A CIPP Liner is<br>pulled into place<br>and the bladder<br>inflated.</p>
      <p class="caption" style="left:397px;top:117px;width:80px">After curing<br>the bladder<br>is removed<br>leaving<br>behind a<br>structrial<br>pipe within<br>a pipe</p>
    </div>

    <div class="cta">
      <p class="cta__web">WWW.DWMPIPE.COM</p>
      <p class="cta__phone">1-800-555-0142</p>
    </div>
    <div class="cta__pill">CALL TODAY FOR ALL YOUR PIPE RESTORATION</div>
  </section>

  <section class="banner banner--side banner--right">
    <div class="brand">
      <div class="brand__row"><span class="brand__mark"></span><span class="brand__name">DWM</span></div>
      <div class="brand__tag">DURABLE WATERLINE METHODS</div>
    </div>
    <div class="card">
      <div class="card__tab">WE FIX</div>
      <div class="fix" style="top:42px">
        <div class="icon"><svg viewBox="0 0 48 48"><path d="M10 6h8M14 6v22a10 10 0 0 0 20 0v-6h8M34 18v8"/></svg></div>
        <div class="fix__label">SLOW<br>DRAINS</div>
      </div>
      <div class="fix" style="top:135px">
        <div class="icon"><svg viewBox="0 0 48 48"><path d="M10 8v24M10 8h16v10c8 0 12 6 12 14"/><path d="M4 36h40M4 41h40"/></svg></div>
        <div class="fix__label">WATER<br>BACK - UPS</div>
      </div>
      <div class="fix" style="top:227px">
        <div class="icon"><svg viewBox="0 0 48 48"><path d="M16 6c-3 4 3 6 0 10s3 6 0 10M24 6c-3 4 3 6 0 10s3 6 0 10M32 6c-3 4 3 6 0 10s3 6 0 10"/><ellipse cx="24" cy="36" rx="16" ry="6"/></svg></div>
        <div class="fix__label">SEWER<br>ODORS</div>
      </div>
      <div class="fix" style="top:322px">
        <div class="icon"><svg viewBox="0 0 48 48"><path d="M4 16v14M44 16v14M4 20h40M4 26h40"/><path d="M24 28c-3 4-3 6 0 8 3-2 3-4 0-8z"/></svg></div>
        <div class="fix__label">CRACKED<br>PIPES</div>
      </div>
      <div class="fix" style="top:415px">
        <div class="icon"><svg viewBox="0 0 48 48"><path d="M4 28v14M44 28v14M4 30h40M4 40h40"/><path d="M24 6v30M24 14c-4-4-8-2-8 2M24 14c4-4 8-2 8 2M24 36l-5 4M24 36l5 4"/></svg></div>
        <div class="fix__label">ROOT<br>INTRUSION</div>
      </div>
      <div class="fix" style="top:509px">
        <div class="icon"><svg viewBox="0 0 48 48"><path d="M6 34V18a6 6 0 0 1 6-6h26M38 8v8"/><path d="M14 24c-2 3 0 5 0 5s2-2 0-5z"/><path d="M22 42l18-14M36 24l6 6"/></svg></div>
        <div class="fix__label">RECURRING<br>PLUMBING<br>PROBLEMS</div>
      </div>
    </div>
    <div class="photo photo--crew" role="img" aria-label="Photo of a crew member operating a green drain cable reel outdoors"></div>
  </section>

</main>
</body>
</html>
```